Website creation for audiovisual activities

I want a website for my director of photography activity. It's primarily composed of screenshots in gallery format, followed by detailed pages for each production.

Here's my current website:
www.lionelbaquet.com
I'd like a more modern and streamlined design, and for the site to be responsive on phones and computers. I also want to be able to easily add photos and text to it later.

Target Market(s)

productions society, directors and producers.

Industry/Entity Type

Audiovisual / TV

Coding

Coded - Design and coding required

Number of Pages Required

5+ page

Font styles to use
Sans Serif

Colors
0054AA
0677BA
7BADD7
CADEEF
E8F1F8
0094D4
00A9DD
6FCCEA
C7EBF8
E9F6FB
00AB8E
00BBA5
67D7C9
C6EFE9
E9F9F6
6B429C
8869AF
B7A5CE
E3DAEB
F3F0F8

Requirements
Must have
• a modern look with a photo gallery on the homepage
Nice to have
• a light background with large, dynamic images
Should not have
• a dark background and an overly classic look

```html
<!DOCTYPE html>
<html lang="fr">
<head>
<meta charset="utf-8">
<title>Mathis Delorme — Directeur de la Photographie</title>
<link rel="stylesheet" href="https://fonts.googleapis.com/css2?family=Poppins:wght@300;400;500;600;700&display=swap">
<style>
:root{
  --blue:#0054AA;
  --blue-mid:#0677BA;
  --cyan:#00A9DD;
  --sky:#E8F1F8;
  --teal:#00AB8E;
  --teal-2:#00BBA5;
  --purple:#6B429C;
  --purple-2:#8869AF;
  --ink:#1d2333;
  --muted:#7a7f8c;
  --footer:#1E3A8E;
  --white:#ffffff;
}
*{box-sizing:border-box;margin:0;padding:0}
html,body{width:1200px;height:3413px;overflow:hidden}
body{font-family:'Poppins',sans-serif;color:var(--ink);background:var(--white);position:relative}
a{color:inherit;text-decoration:none}
.abs{position:absolute}

/* Hero */
.hero{position:absolute;left:0;top:0;width:1200px;height:562px;overflow:hidden}
.hero-photo{position:absolute;inset:0;background:
  radial-gradient(ellipse 420px 300px at 180px 330px,rgba(40,50,90,.9),transparent 70%),
  radial-gradient(ellipse 500px 320px at 950px 350px,rgba(120,90,70,.55),transparent 70%),
  radial-gradient(ellipse 600px 260px at 600px 120px,rgba(70,80,170,.7),transparent 70%),
  linear-gradient(180deg,#2a2f6e 0%,#3a3566 45%,#2b2236 100%)}
.hero-shade{position:absolute;inset:0;background:linear-gradient(180deg,rgba(30,30,90,.35),rgba(20,15,40,.35))}
.nav{position:absolute;left:0;top:0;width:1200px;height:74px}
.logo{position:absolute;left:60px;top:20px;color:#cfd6f2;font-weight:300;font-size:17px;letter-spacing:.5px;line-height:1}
.logo small{display:block;font-size:11px;margin-top:3px;padding-left:22px;letter-spacing:1px}
.nav-link{position:absolute;top:27px;color:#fff;font-size:15px;font-weight:400}
.nav-link.active{font-weight:600;text-decoration:underline;text-underline-offset:3px}
.btn-login{position:absolute;left:892px;top:17px;width:100px;height:40px;border:1.5px solid #fff;border-radius:20px;color:#fff;font-size:14px;display:flex;align-items:center;justify-content:center}
.btn-start{position:absolute;left:1003px;top:17px;width:137px;height:40px;background:var(--purple-2);border-radius:20px;color:#fff;font-size:14px;display:flex;align-items:center;justify-content:center}
.hero-copy{position:absolute;left:0;top:186px;width:1200px;text-align:center;color:#fff}
.hero-eyebrow{font-size:12px;letter-spacing:.5px;color:#8fb6e6;text-transform:uppercase}
.hero-title{font-size:46px;font-weight:600;margin-top:10px;line-height:1.1}
.hero-title span{color:var(--cyan)}
.hero-lead{width:720px;margin:14px auto 0;font-size:21px;font-weight:300;line-height:33px}
.hero-actions{margin-top:28px;display:flex;justify-content:center;gap:13px}
.pill{height:38px;border-radius:19px;font-size:14px;display:inline-flex;align-items:center;gap:8px;padding:0 20px;color:#fff}
.pill.fill{background:var(--purple)}
.pill.ghost{border:1.5px solid #fff}

/* Productions */
.eyebrow{font-size:19px;font-weight:400;color:var(--teal);text-transform:uppercase}
.h2{font-size:30px;font-weight:600;color:var(--blue)}
.see-all{position:absolute;left:841px;top:670px;font-size:19px;color:var(--blue);display:flex;align-items:center;gap:10px}
.card{position:absolute;width:525px}
.card-media{height:306px;border-radius:13px;position:relative;overflow:hidden}
.tag{position:absolute;left:15px;top:15px;height:27px;padding:0 20px;border-radius:14px;color:#fff;font-size:14px;display:flex;align-items:center}
.tag.purple{background:var(--purple)}
.tag.teal{background:var(--teal)}
.corner{position:absolute;right:15px;top:15px;width:33px;height:33px;border-radius:50%;background:rgba(30,30,30,.55);display:flex;align-items:center;justify-content:center}
.card-title{margin-top:10px;font-size:19px;font-weight:600;color:var(--blue)}
.card-meta{margin-top:2px;font-size:13px;color:var(--muted)}
.m1{background:radial-gradient(ellipse at 70% 45%,#6fa8d8 0%,#2a4a6e 30%,#111 75%)}
.m2{background:radial-gradient(ellipse at 50% 45%,#4a8ed6 0%,#1d3f86 40%,#0c1022 80%)}
.m3{background:radial-gradient(ellipse at 50% 20%,#b8e6ff 0%,#1b76c9 30%,#0a1a40 65%,#05060c 100%)}
.m4{background:radial-gradient(ellipse at 60% 30%,#9a7de8 0%,#3447b0 40%,#121632 85%)}

/* Approach */
.approach{position:absolute;left:0;top:1585px;width:1200px;height:585px;background:var(--sky)}
.approach-photo{position:absolute;left:73px;top:47px;width:500px;height:498px;border-radius:10px;background:radial-gradient(ellipse at 45% 40%,#4a4c50 0%,#2a2b2e 55%,#18191b 100%);box-shadow:0 4px 12px rgba(0,0,0,.2)}
.approach-text{position:absolute;left:600px;top:54px;width:560px}
.approach-text .h2{margin-top:8px}
.approach-body{margin-top:18px;font-size:21px;line-height:36.7px;color:var(--ink)}

/* Testimonials */
.testi-head{position:absolute;left:0;top:2240px;width:1200px;text-align:center}
.testi-head h2{font-size:40px;font-weight:700;color:var(--blue)}
.testi-head p{width:720px;margin:12px auto 0;font-size:14px;line-height:23px;color:var(--blue)}
.t-card{position:absolute;top:2438px;width:318px;height:212px;background:#fff;box-shadow:0 8px 24px rgba(20,30,60,.12)}
.quote{position:absolute;left:25px;top:-22px;width:44px;height:44px;border-radius:50%;background:var(--purple);display:flex;align-items:center;justify-content:center}
.stars{position:absolute;left:25px;top:46px;color:#ef8a7f;font-size:14px;letter-spacing:2px}
.t-text{position:absolute;left:25px;top:74px;width:270px;font-size:12.5px;line-height:20px;color:#8a8f99}
.t-card.alt .t-text{color:var(--ink)}
.t-foot{position:absolute;left:0;bottom:0;width:100%;height:60px;border-top:1px solid #eef0f4;display:flex;align-items:center;padding-left:25px;gap:10px}
.avatar{width:30px;height:30px;border-radius:50%;background:#c9ccd3}
.t-name{font-size:11.5px;font-weight:500;color:var(--ink);line-height:1.2}
.t-role{font-size:9px;color:#a3a7b0}

/* CTA */
.cta{position:absolute;left:0;top:2754px;width:1200px;text-align:center}
.cta .eyebrow{text-transform:none;font-size:20px}
.cta .h2{margin-top:10px}
.cta p{width:830px;margin:16px auto 0;font-size:22px;line-height:37px;color:var(--ink)}
.cta .pill{margin-top:28px;height:47px;padding:0 28px;font-size:15px;font-weight:500}

/* Footer */
.footer{position:absolute;left:0;top:3102px;width:1200px;height:311px;background:var(--footer);color:#fff}
.f-rule{position:absolute;height:1px;background:rgba(255,255,255,.25)}
.f-logo{position:absolute;left:83px;top:70px;color:#cdd5f0;font-size:23px;font-weight:300;line-height:1}
.f-logo small{display:block;font-size:16px;padding-left:30px;margin-top:4px;letter-spacing:1px}
.f-desc{position:absolute;left:83px;top:141px;width:400px;font-size:18px;line-height:28px;color:#dfe5f6}
.f-col{position:absolute;top:60px}
.f-col h3{font-size:19px;font-weight:600}
.f-col ul{list-style:none;margin-top:12px}
.f-col li{font-size:15px;line-height:33px}
.f-col li.u a{text-decoration:underline}
.f-col li.b a{font-weight:600;text-decoration:underline}
.copy{position:absolute;left:0;top:274px;width:1200px;text-align:center;font-size:11px}
.social{position:absolute;left:1000px;top:266px;display:flex;gap:10px}
.social span{width:30px;height:30px;border:1.5px solid #fff;border-radius:5px;display:block}
</style>
</head>
<body>

<header class="hero">
  <div class="hero-photo" role="img" aria-label="Photo d'un opérateur en studio devant une console et un ordinateur, lumière bleue et violette"></div>
  <div class="hero-shade"></div>
  <nav class="nav">
    <div class="logo">MATHIS DELORME<small>Directeur Photo</small></div>
    <a class="nav-link active" style="left:245px">Présentation</a>
    <a class="nav-link" style="left:392px">Magazine</a>
    <a class="nav-link" style="left:513px">Émission</a>
    <a class="nav-link" style="left:630px">Événement</a>
    <a class="nav-link" style="left:763px">Conférence</a>
    <a class="btn-login">Login</a>
    <a class="btn-start">Get Started</a>
  </nav>
  <div class="hero-copy">
    <div class="hero-eyebrow">Directeur de la photographie · Paris</div>
    <h1 class="hero-title">Mathis <span>Delorme</span></h1>
    <p class="hero-lead">Capturer l'instant, révéler la lumière. Une vision photographique au service des plus grandes productions audiovisuelles françaises.</p>
    <div class="hero-actions">
      <a class="pill fill">Voir less Production
        <svg width="18" height="10" viewBox="0 0 18 10"><path d="M0 5h16M12 1l4 4-4 4" stroke="#fff" stroke-width="1.6" fill="none"/></svg></a>
      <a class="pill ghost"><svg width="10" height="12" viewBox="0 0 10 12"><path d="M1 1l8 5-8 5z" stroke="#fff" stroke-width="1.3" fill="none"/></svg>Mon Parcours</a>
    </div>
  </div>
</header>

<section>
  <div class="abs eyebrow" style="left:60px;top:632px">Selection</div>
  <h2 class="abs h2" style="left:60px;top:662px">Productios Recentes</h2>
  <a class="see-all">Voir toutes les productions
    <svg width="20" height="12" viewBox="0 0 20 12"><path d="M0 6h18M13 1l5 5-5 5" stroke="#0054AA" stroke-width="1.6" fill="none"/></svg></a>

  <article class="card" style="left:60px;top:733px">
    <div class="card-media m1" role="img" aria-label="DJ aux platines dans une lumière bleue">
      <span class="tag purple" style="top:13px">Emission Live</span>
      <span class="corner"><svg width="12" height="12" viewBox="0 0 12 12"><path d="M2 10L10 2M4 2h6v6" stroke="#fff" stroke-width="1.6" fill="none"/></svg></span>
    </div>
    <div class="card-title">Productios Recentes</div>
    <div class="card-meta">Canal Agora . 2025</div>
  </article>

  <article class="card" style="left:615px;top:733px">
    <div class="card-media m2" role="img" aria-label="Photographe tenant un appareil photo sous un éclairage bleu">
      <span class="tag teal">Documentaire</span>
      <span class="corner"><svg width="12" height="12" viewBox="0 0 12 12"><path d="M2 10L10 2M4 2h6v6" stroke="#fff" stroke-width="1.6" fill="none"/></svg></span>
    </div>
    <div class="card-title">Horizons Lointains</div>
    <div class="card-meta">Canal Agora . 2025</div>
  </article>

  <article class="card" style="left:60px;top:1128px">
    <div class="card-media m3" role="img" aria-label="Foule de concert devant une scène éclairée en bleu">
      <span class="tag teal">Documentaire</span>
      <span class="corner" style="background:none"><svg width="14" height="14" viewBox="0 0 12 12"><path d="M2 10L10 2M4 2h6v6" stroke="#fff" stroke-width="1.6" fill="none"/></svg></span>
    </div>
    <div class="card-title">Maman Chanteuse</div>
    <div class="card-meta">Onde 3 . 2025</div>
  </article>

  <article class="card" style="left:615px;top:1128px">
    <div class="card-media m4" role="img" aria-label="Caméra de plateau et régie sous des projecteurs violets">
      <span class="tag purple">Serie Tv</span>
      <span class="corner" style="background:none"><svg width="14" height="14" viewBox="0 0 12 12"><path d="M2 10L10 2M4 2h6v6" stroke="#fff" stroke-width="1.6" fill="none"/></svg></span>
    </div>
    <div class="card-title">La Ligne de Fuite</div>
    <div class="card-meta">Onde 2 . 2025</div>
  </article>
</section>

<section class="approach">
  <div class="approach-photo" role="img" aria-label="Portrait d'une photographe en veste de cuir avec un appareil sur trépied"></div>
  <div class="approach-text">
    <div class="eyebrow">Mon Approche</div>
    <h2 class="h2">L'image au service de l'histoire</h2>
    <p class="approach-body">Depuis plus de 15 ans, je mets ma vision photographique au service des productions télévisuelles, documentaires et cinématographiques. Mon approche repose sur une écoute attentive du réalisateur et une maîtrise technique au service de l'émotion.<br>Chaque projet est une nouvelle conversation entre la lumière et la narration, entre la technique et la sensibilité artistique.</p>
    <a class="pill fill" style="position:absolute;left:0;top:466px;height:40px;font-size:14px;font-weight:500">En Savoir Plus
      <svg width="18" height="10" viewBox="0 0 18 10"><path d="M0 5h16M12 1l4 4-4 4" stroke="#fff" stroke-width="1.6" fill="none"/></svg></a>
  </div>
</section>

<section>
  <div class="testi-head">
    <h2>What Our Clients Are Saying</h2>
    <p>Lorem ipsum dolor sit amet, consectetur adipiscing elit, sed do eiusmod tempor incididunt ut labore et dolore magna aliqua.</p>
  </div>

  <div class="t-card" style="left:97px">
    <span class="quote"><svg width="16" height="12" viewBox="0 0 16 12"><path d="M1 11V6q0-4 5-5v2q-3 1-3 3h3v5zM9 11V6q0-4 5-5v2q-3 1-3 3h3v5z" fill="#fff"/></svg></span>
    <div class="stars">★★★★★</div>
    <p class="t-text">On the other hand, we denounce with righteous indignation and dislike men who are so beguiled and.</p>
    <div class="t-foot"><span class="avatar"></span><div><div class="t-name">Karel Novak</div><div class="t-role">CEO Studio Nord</div></div></div>
  </div>

  <div class="t-card alt" style="left:440px">
    <span class="quote"><svg width="16" height="12" viewBox="0 0 16 12"><path d="M1 11V6q0-4 5-5v2q-3 1-3 3h3v5zM9 11V6q0-4 5-5v2q-3 1-3 3h3v5z" fill="#fff"/></svg></span>
    <div class="stars">★★★★★</div>
    <p class="t-text">Cum soluta nobis est eligendi optio cumque nihil impedit quo minus id quod maxime placeat facere possimus.</p>
    <div class="t-foot"><span class="avatar"></span><div><div class="t-name">Timo Berger</div><div class="t-role">CEO Vertiga</div></div></div>
  </div>

  <div class="t-card" style="left:785px">
    <span class="quote"><svg width="16" height="12" viewBox="0 0 16 12"><path d="M1 11V6q0-4 5-5v2q-3 1-3 3h3v5zM9 11V6q0-4 5-5v2q-3 1-3 3h3v5z" fill="#fff"/></svg></span>
    <div class="stars">★★★★★</div>
    <p class="t-text">Accusamus et iusto odi ducimus qui blanditiis praesentium voluptatum deleniti atque corrupti quos dolores.</p>
    <div class="t-foot"><span class="avatar"></span><div><div class="t-name">Linnea Holm</div><div class="t-role">CEO Studio Nord</div></div></div>
  </div>
</section>

<section class="cta">
  <div class="eyebrow">Travaillons ensemble</div>
  <h2 class="h2">Vous avez un projet?</h2>
  <p>Que vous soyez réalisateur, producteur ou directeur de production, je serai ravi d'étudier votre projet et d'y apporter ma vision.</p>
  <a class="pill fill">Me Contacter
    <svg width="20" height="10" viewBox="0 0 20 10"><path d="M0 5h18M14 1l4 4-4 4" stroke="#fff" stroke-width="1.6" fill="none"/></svg></a>
</section>

<footer class="footer">
  <div class="f-rule" style="left:593px;top:26px;width:547px"></div>
  <div class="f-logo">MATHIS DELORME<small>Directeur Photo</small></div>
  <p class="f-desc">Directeur de la Photographie et Chef Opérateur pour la télévision, le cinéma et les productions audiovisuelles depuis plus de 15 ans.</p>
  <div class="f-col" style="left:593px">
    <h3>Naviguer</h3>
    <ul>
      <li class="b"><a>Présentation</a></li>
      <li class="u"><a>Magazine</a></li>
      <li class="u"><a>Événement</a></li>
      <li><a>Conférence</a></li>
    </ul>
  </div>
  <div class="f-col" style="left:895px">
    <h3>Connect</h3>
    <ul>
      <li>0612457830</li>
      <li>contact@mathisdelorme.fr</li>
    </ul>
  </div>
  <div class="f-rule" style="left:60px;top:250px;width:1080px"></div>
  <div class="copy">© 2026 Mathis Delorme. All rights reserved.</div>
  <div class="social" aria-label="Réseaux sociaux">
    <span></span><span></span><span></span>
  </div>
</footer>

</body>
</html>
```